Meadowlark Property Review is a leading provider of residential appraisal and home inspection products in S

I need a business card/logo designed that obviously describes my business. We are a residential appraisal and home inspection company in Springfield, MO. We offer residential appraisals, home inspection, pest inspection and radon gas measurement. We have been in business for 18 years and hold state certified residential appraisal licenses and OBREX certified home inspection licenses. I have a logo that I really like and will attach, but would be open to new suggestions. I like more modern designs than traditional and would like a two sided card with our services, licenses and qualifications on the back.

```html
<!DOCTYPE html>
<html lang="en">
<head>
<meta charset="utf-8">
<title>Meadowlark Property Review – Business Card</title>
<link rel="stylesheet" href="https://fonts.googleapis.com/css2?family=Source+Sans+3:wght@400;600&display=swap">
<style>
  :root {
    --backdrop: #000000;
    --card: #323337;
    --divider: #4a4b50;
    --tan: #b08a57;
    --orange: #f7941d;
    --ink: #ffffff;
    --ink-soft: #d6d6d8;
  }
  * { margin: 0; padding: 0; box-sizing: border-box; }
  html, body {
    width: 1200px;
    height: 900px;
    overflow: hidden;
    background: var(--backdrop);
  }
  body {
    position: relative;
    font-family: "Source Sans 3", "Myriad Pro", sans-serif;
  }
  .card {
    position: absolute;
    top: 271px;
    width: 457px;
    height: 281px;
    border-radius: 16px;
    background: var(--card);
  }
  .card--front { left: 137px; }
  .card--back { left: 626px; }

  /* Front */
  .front-brand {
    position: absolute;
    left: 30px;
    top: 108px;
    width: 200px;
    text-align: center;
  }
  .front-brand__name {
    color: var(--orange);
    font-weight: 600;
    font-size: 19px;
    line-height: 1.15;
  }
  .front-brand__tagline {
    margin-top: 6px;
    color: var(--tan);
    font-size: 9px;
    letter-spacing: 2px;
    text-transform: uppercase;
  }
  .front-divider {
    position: absolute;
    left: 237px;
    top: 78px;
    width: 1px;
    height: 128px;
    background: var(--divider);
  }
  .contact {
    position: absolute;
    left: 249px;
    top: 62px;
    color: var(--ink);
    font-size: 13px;
    line-height: 16px;
  }
  .contact__name {
    font-size: 19px;
    line-height: 24px;
    color: var(--tan);
  }
  .contact__name .surname { color: var(--orange); }
  .contact__title { margin-bottom: 11px; }
  .contact__address { margin-bottom: 10px; }
  .contact__line {
    display: flex;
    align-items: center;
    gap: 7px;
    padding-left: 3px;
  }
  .contact__line svg { width: 9px; height: 9px; flex: none; }

  /* Back */
  .back-brand {
    position: absolute;
    left: 0;
    right: 0;
    top: 78px;
    text-align: center;
  }
  .back-brand__name {
    color: var(--orange);
    font-weight: 600;
    font-size: 27px;
    line-height: 32px;
    letter-spacing: 0.3px;
  }
  .back-brand__tagline {
    margin-top: 6px;
    color: var(--tan);
    font-size: 11px;
    letter-spacing: 4px;
    text-transform: uppercase;
  }
  .back-rule {
    position: absolute;
    left: 128px;
    top: 150px;
    width: 201px;
    height: 1px;
    background: var(--divider);
  }
  .services {
    position: absolute;
    left: 30px;
    right: 30px;
    top: 166px;
    display: flex;
    flex-wrap: wrap;
    justify-content: center;
    gap: 4px 14px;
    list-style: none;
    color: var(--ink);
    font-size: 12px;
    line-height: 16px;
  }
  .services li { display: flex; align-items: center; gap: 6px; }
  .services li::before {
    content: "";
    width: 5px;
    height: 5px;
    background: var(--orange);
  }
  .credentials {
    position: absolute;
    left: 30px;
    right: 30px;
    top: 214px;
    text-align: center;
    color: var(--ink-soft);
    font-size: 11px;
    line-height: 15px;
  }
  .credentials strong { color: var(--tan); font-weight: 600; }
</style>
</head>
<body>
  <section class="card card--front">
    <div class="front-brand">
      <p class="front-brand__name">Meadowlark<br>Property Review</p>
      <p class="front-brand__tagline">Appraisal &amp; Inspection</p>
    </div>
    <div class="front-divider"></div>
    <div class="contact">
      <p class="contact__name">Daniel <span class="surname">Harper</span></p>
      <p class="contact__title">Managing Director</p>
      <p class="contact__address">4821 Cedar Ridge Lane<br>Country Name, 123456.</p>
      <p class="contact__line">
        <svg viewBox="0 0 10 10" aria-hidden="true"><path fill="#f7941d" d="M1 3 Q5 0 9 3 L8 4.5 L6.5 3.8 L6.3 3 H3.7 L3.5 3.8 L2 4.5 Z M2 5 H8 L8.5 9 H1.5 Z"/></svg>
        044-208 315 742
      </p>
      <p class="contact__line">
        <svg viewBox="0 0 10 10" aria-hidden="true"><rect x="0.5" y="2" width="9" height="6.5" fill="#f7941d"/><path d="M0.5 2 L5 5.8 L9.5 2" fill="none" stroke="#323337" stroke-width="1"/></svg>
        hello@meadowlark.com
      </p>
      <p class="contact__line">
        <svg viewBox="0 0 10 10" aria-hidden="true"><g fill="none" stroke="#f7941d" stroke-width="1.6" stroke-linecap="round"><path d="M4 6 L6 4"/><path d="M3.2 4.6 L1.9 5.9 a1.6 1.6 0 0 0 2.2 2.2 L5.4 6.8"/><path d="M6.8 5.4 L8.1 4.1 a1.6 1.6 0 0 0 -2.2 -2.2 L4.6 3.2"/></g></svg>
        www.meadowlark.com
      </p>
    </div>
  </section>

  <section class="card card--back">
    <div class="back-brand">
      <p class="back-brand__name">Meadowlark Property Review</p>
      <p class="back-brand__tagline">Residential Appraisal &amp; Home Inspection</p>
    </div>
    <div class="back-rule"></div>
    <ul class="services">
      <li>Residential Appraisals</li>
      <li>Home Inspection</li>
      <li>Pest Inspection</li>
      <li>Radon Gas Measurement</li>
    </ul>
    <p class="credentials">
      <strong>State Certified</strong> Residential Appraiser · <strong>OBREX Certified</strong> Home Inspector<br>
      Serving Springfield, MO for 18 Years
    </p>
  </section>
</body>
</html>
```